Design logo, business cards, and web page for new web and bi development consulting company

I've started a Web and Business Intelligence development consulting company. We develop on Quordex's stack, Veltrix Studio and Tabula Server. We develop responsive web sites and business intelligence platforms. I plan on focusing on small to medium sized business as my client base. I need a logo, business cards, and a one page web site. We will do more with the web site with you in the next six months if the business survives. The name of the company is Corvalo Integration Solutions, Corvalo for short.

Target Market(s)

small to medium sized businesses

Industry/Entity Type

Business

Contact Information for Business Card

logo
name
title
email
phone

Logo Text

Corvalo Integration Solutions - web and data solutions

Coding

Coded - Design and coding required

Number of Pages Required

1 page

Font styles to use
Sans Serif

Colors
0355a3
0092cd
00a88f
6b449b

Requirements
Nice to have
• web and data solutions

```html
<!DOCTYPE html>
<html lang="en">
<head>
<meta charset="utf-8">
<title>Corvalo Integration Solutions</title>
<link rel="stylesheet" href="https://fonts.googleapis.com/css2?family=Lato:wght@400;700;900&family=Open+Sans:wght@400;600;700&family=Oswald:wght@400&display=swap">
<style>
:root{
  --brand:#1a7cc4;
  --brand-dark:#0d3f8a;
  --navy:#0b2f6b;
  --heading-blue:#0b4ea2;
  --ink:#222;
  --muted:#8a8a8a;
  --panel:#efefef;
  --footer:#222222;
  --white:#fff;
}
*{box-sizing:border-box;margin:0;padding:0}
html,body{width:1200px;height:2270px;overflow:hidden;background:var(--white)}
body{position:relative;font-family:"Open Sans",Arial,sans-serif;color:var(--ink)}
h1,h2,h3{font-weight:400}
.abs{position:absolute}
/* header */
.site-header{top:0;left:0;width:1200px;height:106px;background:var(--white)}
.brand{left:0;width:1200px;top:22px;display:flex;justify-content:center;align-items:center;gap:10px}
.brand-mark{width:34px;height:34px;border-radius:50%;background:var(--brand)}
.brand-name{color:var(--heading-blue);font-weight:700;line-height:1}
.brand-name .big{display:block;font-size:32px}
.brand-name .small{display:block;font-size:12px;margin-top:3px}
/* nav */
.main-nav{top:106px;left:0;width:1200px;height:73px;background:var(--brand)}
.nav-links{left:89px;top:0;height:73px;display:flex;list-style:none}
.nav-links li{height:73px;line-height:73px;padding:0 15px;color:var(--white);font-size:16px}
.nav-links li.active{background:var(--brand-dark);width:90px;text-align:center;padding:0}
.search{left:908px;top:21px;width:205px;height:30px;background:var(--white);border-radius:3px;box-shadow:inset 0 0 0 2px #d7e6f3;font-size:10px;color:#999;padding:8px 10px}
.search svg{position:absolute;right:10px;top:9px}
/* hero */
.hero{top:179px;left:0;width:1200px;height:564px;background:radial-gradient(ellipse at 65% 45%,#3d78a8 0%,#1a3c5e 35%,#0a1624 70%,#05090f 100%)}
.hero-title{left:144px;top:218px;width:940px;color:var(--white);font-family:Lato,sans-serif;font-weight:700;font-size:44px;line-height:56px}
.hero-arrow{top:265px;width:36px;height:36px;border:2px solid var(--white);border-radius:50%}
.hero-arrow svg{position:absolute;left:7px;top:7px}
/* cta */
.cta{top:673px;left:89px;width:1023px;height:139px;background:var(--brand);box-shadow:0 4px 8px rgba(0,0,0,.3)}
.cta-title{left:49px;top:36px;color:var(--white);font-family:Lato,sans-serif;font-weight:700;font-size:25px}
.cta-sub{left:49px;top:76px;color:var(--white);font-family:Lato,sans-serif;font-weight:700;font-size:17px}
.cta-button{left:765px;top:45px;width:208px;height:49px;background:var(--navy);border-radius:4px;color:var(--white);font-family:Lato,sans-serif;font-weight:700;font-size:17px;line-height:49px;padding-left:28px;box-shadow:0 2px 4px rgba(0,0,0,.3)}
.cta-button svg{position:absolute;right:16px;top:17px}
/* welcome */
.welcome-title{top:852px;left:0;width:1200px;text-align:center;font-size:27px;color:var(--ink)}
.welcome-text{top:897px;left:170px;width:860px;text-align:center;font-size:12.5px;line-height:21px;color:var(--muted)}
.service{top:993px;width:300px;text-align:center}
.service-badge{margin:0 auto;width:138px;height:138px;border-radius:50%;background:var(--white);box-shadow:inset 0 0 0 8px #e4e4e4,0 1px 3px rgba(0,0,0,.2);display:flex;align-items:center;justify-content:center;font-size:15px;color:#555;font-weight:600;padding:0 14px;text-align:center}
.service-title{margin-top:17px;font-size:20px;color:var(--heading-blue)}
.service-text{margin:8px auto 0;width:270px;font-size:11.5px;line-height:21px;color:var(--muted)}
.read-more{margin-top:12px;font-size:12px;color:var(--ink);letter-spacing:.3px}
/* split */
.split-photo{top:1326px;left:0;width:601px;height:339px;background:linear-gradient(90deg,#2c3b52 0%,#8aa0b8 40%,#d9dfe6 75%,#eef1f4 100%)}
.split-panel{top:1326px;left:601px;width:599px;height:339px;background:var(--panel)}
.quote{left:44px;top:32px;width:470px;font-weight:700;font-size:16px;line-height:26px;color:var(--ink)}
.split-text{left:44px;top:104px;width:202px;font-size:11px;line-height:21px;color:var(--muted);text-align:justify}
.split-more{left:44px;top:275px;font-size:16px;color:var(--heading-blue)}
.split-more svg{vertical-align:middle;margin-left:14px}
.pill{left:278px;width:233px;height:37px;background:var(--brand);color:var(--white);font-size:12.5px;line-height:37px;padding-left:15px;white-space:nowrap}
.split-side{left:288px;top:162px;width:215px;font-size:11px;line-height:21px;color:var(--muted);text-align:justify}
/* news */
.news-title{top:1705px;left:0;width:1200px;text-align:center;font-size:26px}
.news-item{top:1755px;width:325px}
.news-date{position:absolute;left:0;top:0;width:95px;height:75px;border-right:1px solid #ccc}
.news-day{font-family:Oswald,sans-serif;font-size:44px;line-height:48px;color:var(--brand)}
.news-month{font-size:14px;color:var(--brand)}
.news-head{position:absolute;left:118px;top:12px;width:230px;font-size:15px;line-height:22px;color:var(--ink)}
.news-text{position:absolute;left:0;top:92px;width:320px;font-size:11.5px;line-height:21px;color:var(--muted)}
.news-link{position:absolute;left:0;top:142px;font-size:13px;color:var(--heading-blue);text-decoration:underline}
.news-link svg{position:absolute;left:133px;top:4px}
.divider{top:1957px;left:0;width:1200px;height:1px;background:#e6e6e6}
/* contact */
.contact-card{top:2025px;width:219px;height:128px;background:var(--panel);text-align:center}
.contact-icon{position:absolute;left:77px;top:-32px;width:64px;height:64px;border-radius:50%;background:var(--brand);display:flex;align-items:center;justify-content:center}
.contact-title{margin-top:46px;font-size:16px;color:var(--ink)}
.contact-text{margin-top:6px;font-size:11.5px;line-height:18px;color:var(--muted)}
.social-dots{margin-top:10px;display:flex;justify-content:center;gap:11px}
.social-dots span{width:17px;height:17px;border-radius:50%;background:#777}
/* footer */
.site-footer{top:2196px;left:0;width:1200px;height:74px;background:var(--footer);color:var(--white);font-size:11px}
.copyright{left:89px;top:30px}
.footer-links{left:802px;top:30px;display:flex;list-style:none}
.footer-links li{margin-right:29px}
</style>
</head>
<body>

<header class="site-header abs">
  <div class="brand abs">
    <span class="brand-mark"></span>
    <span class="brand-name"><span class="big">Corvalo</span><span class="small">Integration Solutions</span></span>
  </div>
</header>

<nav class="main-nav abs">
  <ul class="nav-links abs">
    <li class="active">Home</li><li>About us</li><li>Services</li><li>News</li><li>Contacts</li>
  </ul>
  <div class="search abs">Search....
    <svg width="11" height="11" viewBox="0 0 11 11"><circle cx="4.5" cy="4.5" r="3.5" fill="none" stroke="#bbb" stroke-width="1.3"/><line x1="7" y1="7" x2="10" y2="10" stroke="#bbb" stroke-width="1.3"/></svg>
  </div>
</nav>

<section class="hero abs" role="img" aria-label="Photo of a hand holding a laptop surrounded by glowing network nodes, envelopes and a world map">
  <h1 class="hero-title abs">Nam libero tempore, cum soluta nobis est eligendi optio cumque nihil impedit quo minus!!</h1>
  <div class="hero-arrow abs" style="left:52px"><svg width="18" height="18" viewBox="0 0 18 18"><path d="M16 9H3M8 4 3 9l5 5" fill="none" stroke="#fff" stroke-width="1.8"/></svg></div>
  <div class="hero-arrow abs" style="left:1112px"><svg width="18" height="18" viewBox="0 0 18 18"><path d="M2 9h13M10 4l5 5-5 5" fill="none" stroke="#fff" stroke-width="1.8"/></svg></div>
</section>

<section class="cta abs">
  <h2 class="cta-title abs">Lorem ipsum dolor sit amet, consectetur adipisicing sed et</h2>
  <p class="cta-sub abs">Eiusmod tempor incididunt ut labore et dolore magna aliqua.</p>
  <div class="cta-button abs">LEARN MORE
    <svg width="16" height="16" viewBox="0 0 16 16"><circle cx="8" cy="8" r="8" fill="#fff"/><path d="M4 8h7M8 5l3 3-3 3" fill="none" stroke="#0b2f6b" stroke-width="1.8"/></svg>
  </div>
</section>

<h2 class="welcome-title abs">Welcome to Corvalo Integration Solutions</h2>
<p class="welcome-text abs">Epsum dolor sit amet, consectetur adipisicing elit sed ut labore et dolore magna aliquautenim ad minim veniam, quis nostrud exercitation ullamco laboris nisi.Lorem ipsum dolor sit amet, consectetur adipisicing elit sed dobe eiusmod tempor incidut labore et dolore magna aliquautenad minim veniam, quis nostrud.</p>

<article class="service abs" style="left:102px">
  <div class="service-badge">Quordex</div>
  <h3 class="service-title">Quordex's stack</h3>
  <p class="service-text">Sed ut perspiciatis unde omnis istetus error sit voluptatem accusantium doloremque laudantium, totrem aperiam, eaque ipsa quae ab illo inventore veritatis et quasi beatae.</p>
  <div class="read-more">READ MORE &nbsp;→</div>
</article>
<article class="service abs" style="left:444px">
  <div class="service-badge">Veltrix Studio</div>
  <h3 class="service-title">Veltrix Studio</h3>
  <p class="service-text">Sed ut perspiciatis unde omnis istetus error sit voluptatem accusantium doloremque laudantium, totrem aperiam, eaque ipsa quae ab illo inventore veritatis et quasi beatae.</p>
  <div class="read-more">READ MORE &nbsp;→</div>
</article>
<article class="service abs" style="left:787px">
  <div class="service-badge">Tabula Server</div>
  <h3 class="service-title">Tabula Server</h3>
  <p class="service-text">Sed ut perspiciatis unde omnis istetus error sit voluptatem accusantium doloremque laudantium, totrem aperiam, eaque ipsa quae ab illo inventore veritatis et quasi beatae.</p>
  <div class="read-more">READ MORE &nbsp;→</div>
</article>

<div class="split-photo abs" role="img" aria-label="Photo of a businessman in suit and tie in an office, with colleagues at a meeting table behind him"></div>
<section class="split-panel abs">
  <blockquote class="quote abs">“ Vivamus ac ultrices diam, vitae accumsan tellus. Integer vulputate lacus, congue vulputate nisl eleifend in ”</blockquote>
  <p class="split-text abs">Proin gravida nibh vel velit auctor aliquet. Aenean sollicitudin, lorem quis bibendum auctor, nisi elit consequat ipsum, nec sagittis sem nibh id elit.Nunc non mollis nulla. Sed tconsectetur elit id mi consectetur bibendum.....</p>
  <div class="split-more abs">Read More<svg width="18" height="10" viewBox="0 0 18 10"><path d="M0 5h15M11 1l4 4-4 4" fill="none" stroke="#0b4ea2" stroke-width="2"/></svg></div>
  <div class="pill abs" style="top:107px">We Develop Responsive Websites</div>
  <p class="split-side abs">Lorem ipsum dolor sit amet, consectetur adipiscing elit. Vestibulum nec odio ipsum. Suspendisse cursus malesuada facilisis...</p>
  <div class="pill abs" style="top:264px">Business Intelligence Platforms</div>
</section>

<h2 class="news-title abs">Latest News</h2>
<article class="news-item abs" style="left:89px">
  <div class="news-date"><div class="news-day">23</div><div class="news-month">January</div></div>
  <h3 class="news-head">Ut enim ad minim veniamquis nostrud ullamco in volup.</h3>
  <p class="news-text">Tempore, cum soluta nobis est eligendi opticumque nihil quo impedit quo minus id quod repellendusemporibus...</p>
  <div class="news-link">Continue Reading<svg width="10" height="8" viewBox="0 0 10 8"><path d="M0 4h8M5 1l3 3-3 3" fill="none" stroke="#555" stroke-width="1"/></svg></div>
</article>
<article class="news-item abs" style="left:438px">
  <div class="news-date"><div class="news-day">17</div><div class="news-month">February</div></div>
  <h3 class="news-head">Ut enim ad minim veniamquis nostrud ullamco in volup.</h3>
  <p class="news-text">Tempore, cum soluta nobis est eligendi opticumque nihil quo impedit quo minus id quod repellendusemporibus...</p>
  <div class="news-link">Continue Reading<svg width="10" height="8" viewBox="0 0 10 8"><path d="M0 4h8M5 1l3 3-3 3" fill="none" stroke="#555" stroke-width="1"/></svg></div>
</article>
<article class="news-item abs" style="left:787px">
  <div class="news-date"><div class="news-day">20</div><div class="news-month">February</div></div>
  <h3 class="news-head">Ut enim ad minim veniamquis nostrud ullamco in volup.</h3>
  <p class="news-text">Tempore, cum soluta nobis est eligendi opticumque nihil quo impedit quo minus id quod repellendusemporibus...</p>
  <div class="news-link">Continue Reading<svg width="10" height="8" viewBox="0 0 10 8"><path d="M0 4h8M5 1l3 3-3 3" fill="none" stroke="#555" stroke-width="1"/></svg></div>
</article>

<div class="divider abs"></div>

<section class="contact-card abs" style="left:106px">
  <div class="contact-icon"><svg width="22" height="30" viewBox="0 0 22 30"><path d="M11 1C5.5 1 1 5.3 1 10.8 1 18 11 29 11 29s10-11 10-18.2C21 5.3 16.5 1 11 1z" fill="#fff"/><circle cx="11" cy="11" r="4" fill="#1a7cc4"/></svg></div>
  <h3 class="contact-title">Our Address</h3>
  <p class="contact-text">1234, Street Name, City Name,<br>Country Name..</p>
</section>
<section class="contact-card abs" style="left:363px">
  <div class="contact-icon"><svg width="26" height="26" viewBox="0 0 26 26"><path d="M6 2l4 5-2.5 3c1.5 3.5 4.5 6.5 8 8l3-2.5 5 4-2.5 4C12 23 3 14 2 5z" fill="#fff"/></svg></div>
  <h3 class="contact-title">Call Us</h3>
  <p class="contact-text">+1 (555) 0142 000<br>+1 (555) 0142 000</p>
</section>
<section class="contact-card abs" style="left:620px">
  <div class="contact-icon"><svg width="30" height="22" viewBox="0 0 30 22"><rect x="1" y="1" width="28" height="20" rx="2" fill="#fff"/><path d="M2 3l13 10L28 3" fill="none" stroke="#1a7cc4" stroke-width="2"/></svg></div>
  <h3 class="contact-title">Email Us</h3>
  <p class="contact-text">info@CorvaloSolutions.com<br>support@CorvaloSolutions.com</p>
</section>
<section class="contact-card abs" style="left:874px">
  <div class="contact-icon"><svg width="28" height="28" viewBox="0 0 28 28"><rect x="2" y="12" width="6" height="14" rx="1" fill="#fff"/><path d="M10 13l5-10c2 0 3 1.5 2.5 4L16.5 11H24c2 0 3 1.5 2.5 3.5l-2 9c-.4 1.6-1.5 2.5-3 2.5H10z" fill="#fff"/></svg></div>
  <h3 class="contact-title">Get Socialize</h3>
  <div class="social-dots"><span></span><span></span><span></span><span></span><span></span></div>
</section>

<footer class="site-footer abs">
  <p class="copyright abs">Copyright © 2015 Corvalo Integration Solutions. All Right Reserved</p>
  <ul class="footer-links abs"><li>Home</li><li>About us</li><li>Services</li><li>News</li><li>Contacts</li><li>C13</li></ul>
</footer>

</body>
</html>
```